iOS7 test prep app

I need 3 basic screens and 2 product images for an iOS7 app I am prototyping. I provided lots of detail in the attached brief. This is an education product, so warm colors (especially reds) work best.

If you've done flat design for mobile products, please take a look ... Thanks!

Greetings, all. Thank you for your submissions. I am meeting with my product development team this week to review your submissions, and will select a designer before the end of the week. I appreciate your patience with my process, and thank you again for your interest in my project. I'll be back to you soon ... -Gerald

```html
<!DOCTYPE html>
<html lang="en">
<head>
<meta charset="utf-8">
<title>Test Prep – Q&amp;A Screens</title>
<link href="https://fonts.googleapis.com/css2?family=Roboto+Condensed:wght@400;700&family=Roboto:wght@400;700&display=swap" rel="stylesheet">
<style>
:root{
  --canvas:#dfd8cc;
  --shadow-a:#a8a49d;
  --shadow-b:#9f9b95;
  --orange:#f19a17;
  --orange-top:#f4a524;
  --orange-bottom:#ee8a0b;
  --orange-dark:#e8820a;
  --ink:#222222;
  --text:#333333;
  --muted:#8a8a8a;
  --panel:#e6e6e6;
  --band:#f4f4f4;
  --white:#ffffff;
  --rule:#d4d4d4;
  --wrong:#e3262b;
  --right:#2fb43b;
  --black-btn:#1a1a1a;
}
*{box-sizing:border-box;margin:0;padding:0}
html,body{width:1200px;height:1000px;overflow:hidden}
body{background:var(--canvas);position:relative;font-family:"Roboto",Helvetica,Arial,sans-serif;color:var(--text)}
.shadows{position:absolute;left:0;top:0}
.screen-title{position:absolute;top:30px;width:479px;text-align:center;font-family:"Roboto Condensed",sans-serif;font-size:40px;color:#111;letter-spacing:.3px}
.phone{position:absolute;top:119px;width:479px;height:851px;background:var(--panel);overflow:hidden}
.phone--one{left:107px}
.phone--two{left:620px}
.app-bar{height:95px;background:linear-gradient(var(--orange-top),var(--orange-bottom));position:relative;color:var(--white)}
.status-bar{height:29px;display:flex;align-items:center;justify-content:space-between;padding:0 8px 0 10px;font-size:16px}
.status-bar .carrier{display:flex;align-items:center;gap:4px}
.status-bar .time{position:absolute;left:0;right:0;text-align:center;pointer-events:none}
.status-bar .battery{display:flex;align-items:center;gap:4px}
.back-button{position:absolute;left:10px;top:41px;width:61px;height:44px;border-radius:22px;background:var(--orange-dark);border:1px solid #d97508;display:flex;align-items:center;justify-content:center}
.bar-title{position:absolute;left:0;right:0;top:46px;text-align:center;font-family:"Roboto Condensed",sans-serif;font-weight:700;font-size:26px}
.question{background:var(--white);height:129px;padding:9px 13px 0 14px;font-size:17px;line-height:27px;text-align:justify;text-indent:24px;border-bottom:1px solid var(--rule)}
.answers{list-style:none;padding:14px 14px 0 14px}
.answer{height:52px;background:var(--white);margin-bottom:15.5px;display:flex;align-items:center;padding-left:20px;font-size:17px;box-shadow:0 1px 1px rgba(0,0,0,.12)}
.answer--wrong{border-left:4px solid var(--wrong);padding-left:16px}
.answer--right{border-left:4px solid var(--right);padding-left:16px;font-weight:700}
.confidence{position:absolute;top:546px;left:0;right:0}
.confidence-label{height:41px;background:var(--band);text-align:center;font-family:"Roboto Condensed",sans-serif;font-size:19px;line-height:41px;color:var(--ink)}
.confidence-scale{height:97px;background:var(--white);position:relative;border-bottom:1px solid var(--rule)}
.scale-numbers{position:absolute;top:56px;left:24px;right:24px;display:flex;justify-content:space-between;font-size:15px;color:var(--muted)}
.explanation{position:absolute;top:546px;left:0;right:0;height:138px;background:var(--white);padding:15px 14px 0 13px;font-size:17px;line-height:27px;text-align:justify;text-indent:28px;border-bottom:1px solid var(--rule)}
.explanation strong{font-weight:700;color:var(--ink)}
.button{position:absolute;top:742px;height:65px;display:flex;align-items:center;justify-content:center;font-family:"Roboto Condensed",sans-serif;font-size:28px;color:var(--white);box-shadow:0 2px 2px rgba(0,0,0,.15)}
.button--submit{left:42px;width:396px;background:linear-gradient(var(--orange-top),var(--orange-bottom))}
.button--save{left:20px;width:207px;background:var(--black-btn);font-weight:700;font-size:26px}
.button--next{left:250px;width:208px;background:linear-gradient(var(--orange-top),var(--orange-bottom));font-weight:700;font-size:26px}
</style>
</head>
<body>
<svg class="shadows" width="1200" height="1000" aria-hidden="true">
  <polygon points="586,119 1586,1119 1107,1970 107,970" fill="var(--shadow-a)"/>
  <polygon points="1099,119 2099,1119 1620,1970 620,970" fill="var(--shadow-b)"/>
</svg>

<h2 class="screen-title" style="left:107px">Q&amp;A Screen 1</h2>
<h2 class="screen-title" style="left:620px">Q&amp;A Screen 2</h2>

<section class="phone phone--one">
  <header class="app-bar">
    <div class="status-bar">
      <span class="carrier">●●●○○ Nexa
        <svg width="16" height="12" viewBox="0 0 16 12"><path d="M8 11 L5.5 8.2 A3.6 3.6 0 0 1 10.5 8.2Z M2.8 5.6 A7.4 7.4 0 0 1 13.2 5.6 L12 7 A5.6 5.6 0 0 0 4 7Z M0.3 3 A11 11 0 0 1 15.7 3 L14.5 4.3 A9.2 9.2 0 0 0 1.5 4.3Z" fill="#fff"/></svg></span>
      <span class="time">7:28 PM</span>
      <span class="battery">100%
        <svg width="36" height="14" viewBox="0 0 36 14"><rect x="0.5" y="0.5" width="32" height="13" rx="2" fill="none" stroke="#fff"/><rect x="2" y="2" width="29" height="10" fill="#fff"/><rect x="33.5" y="4.5" width="2" height="5" fill="#fff"/></svg></span>
    </div>
    <div class="back-button"><svg width="14" height="22" viewBox="0 0 14 22"><path d="M11 2 L3 11 L11 20" fill="none" stroke="#fff" stroke-width="3" stroke-linecap="round" stroke-linejoin="round"/></svg></div>
    <div class="bar-title">Question 7 of 100</div>
  </header>
  <p class="question">A patient presents to the emergency room with the following symptoms: Anxiety, dyspnea, rhonchi, fever, Oxygen saturation of 88%, and a pH of 7.21. The nurse realized that the patient suffering from:</p>
  <ul class="answers">
    <li class="answer">A. Respiratory alkalosis</li>
    <li class="answer">B. Metabolic alkalosis</li>
    <li class="answer">C. Respiratory acidosis</li>
    <li class="answer">D. Metabolic acidosis</li>
  </ul>
  <div class="confidence">
    <div class="confidence-label">CONFIDENCE</div>
    <div class="confidence-scale">
      <svg width="479" height="60" style="position:absolute;left:0;top:10px">
        <line x1="24" y1="25" x2="239" y2="25" stroke="var(--orange)" stroke-width="1.5"/>
        <line x1="239" y1="25" x2="455" y2="25" stroke="#999" stroke-width="1.5"/>
        <circle cx="239" cy="25" r="13" fill="var(--orange)"/>
      </svg>
      <div class="scale-numbers"><span>1</span><span>2</span><span>3</span><span>4</span><span>5</span><span>6</span><span>7</span></div>
    </div>
  </div>
  <div class="button button--submit">SUBMIT</div>
</section>

<section class="phone phone--two">
  <header class="app-bar">
    <div class="status-bar">
      <span class="carrier">●●●○○ Nexa
        <svg width="16" height="12" viewBox="0 0 16 12"><path d="M8 11 L5.5 8.2 A3.6 3.6 0 0 1 10.5 8.2Z M2.8 5.6 A7.4 7.4 0 0 1 13.2 5.6 L12 7 A5.6 5.6 0 0 0 4 7Z M0.3 3 A11 11 0 0 1 15.7 3 L14.5 4.3 A9.2 9.2 0 0 0 1.5 4.3Z" fill="#fff"/></svg></span>
      <span class="time">7:28 PM</span>
      <span class="battery">100%
        <svg width="36" height="14" viewBox="0 0 36 14"><rect x="0.5" y="0.5" width="32" height="13" rx="2" fill="none" stroke="#fff"/><rect x="2" y="2" width="29" height="10" fill="#fff"/><rect x="33.5" y="4.5" width="2" height="5" fill="#fff"/></svg></span>
    </div>
    <div class="back-button"><svg width="14" height="22" viewBox="0 0 14 22"><path d="M11 2 L3 11 L11 20" fill="none" stroke="#fff" stroke-width="3" stroke-linecap="round" stroke-linejoin="round"/></svg></div>
    <div class="bar-title">Question 7 of 100</div>
  </header>
  <p class="question">A patient presents to the emergency room with the following symptoms: Anxiety, dyspnea, rhonchi, fever, Oxygen saturation of 88%, and a pH of 7.21. The nurse realized that the patient suffering from:</p>
  <ul class="answers">
    <li class="answer answer--wrong">A. Respiratory alkalosis</li>
    <li class="answer answer--wrong">B. Metabolic alkalosis</li>
    <li class="answer answer--right">C. Respiratory acidosis</li>
    <li class="answer answer--wrong">D. Metabolic acidosis</li>
  </ul>
  <p class="explanation"><strong>The correct answer is Letter C.</strong> A key symptom of respiratory distress syndrome is the inability of the respiratory system to exchange gases, resulting in respiratory acidosis.</p>
  <div class="button button--save">SAVE &amp; CLOSE</div>
  <div class="button button--next">NEXT QUESTION</div>
</section>
</body>
</html>
```